showcase project portfolio

create power point of project portfolio
from word file and website using similar design template

https://www.brelmor.co.uk/

Target Market(s)

corporte

```html
<!DOCTYPE html>
<html lang="en">
<head>
<meta charset="utf-8">
<title>Brelmor – Project Portfolio Template</title>
<link href="https://fonts.googleapis.com/css2?family=Montserrat:wght@800;900&family=Quicksand:wght@300;400;500;600;700&display=swap" rel="stylesheet">
<style>
:root{
  --board:#5f727b;
  --navy:#1f3a57;
  --navy-deep:#162b42;
  --tan:#c8a386;
  --tan-soft:rgba(200,163,134,.78);
  --paper:#eeeeee;
  --white:#ffffff;
  --ink:#2c3e50;
  --muted:#7b8794;
}
*{box-sizing:border-box;margin:0;padding:0}
html,body{width:1051px;height:1200px;overflow:hidden;background:var(--board)}
body{position:relative;font-family:"Quicksand",sans-serif;color:var(--ink)}
h1,h2,h3,h4,h5{font-weight:400}
.slide{position:absolute;width:474px;height:266px;overflow:hidden;background:var(--paper);box-shadow:0 2px 4px rgba(0,0,0,.25)}
.col-a{left:39px}.col-b{left:549px}
.row-1{top:39px}.row-2{top:325px}.row-3{top:612px}.row-4{top:902px}

/* logo tab */
.logo-tab{position:absolute;left:0;top:0;width:68px;height:38px;background:var(--white);border-bottom-right-radius:22px;display:flex;align-items:center;justify-content:center;gap:3px;z-index:3}
.logo-tab.large{width:117px;height:66px;border-bottom-right-radius:38px}
.wordmark{font-family:"Quicksand",sans-serif;font-weight:700;color:var(--navy);letter-spacing:.06em;font-size:8px}
.logo-tab.large .wordmark{font-size:13px}
.mark-dot{width:5px;height:5px;border-radius:50%;background:var(--tan)}
.logo-tab.large .mark-dot{width:8px;height:8px}

/* footer */
.footer-band{position:absolute;left:257px;bottom:0;width:217px;height:19px;background:var(--navy);display:flex;align-items:center;justify-content:flex-end;padding-right:26px;z-index:3}
.site{font-size:8px;letter-spacing:.2em;color:var(--tan);font-weight:500}
.page-badge{position:absolute;right:10px;top:3px;width:14px;height:14px;border-radius:50%;background:var(--white);color:var(--navy);font-size:3.6px;line-height:4px;text-align:center;padding-top:3px}
.plain-circle{position:absolute;right:10px;top:3px;width:14px;height:14px;border-radius:50%;background:var(--white)}

.photo{position:absolute}
.body-text{font-size:4.6px;line-height:6.4px;color:var(--muted)}

/* cover */
.cover .photo{inset:0;background:linear-gradient(160deg,#5c6b72 0%,#2e3a42 40%,#1b242b 75%,#232a2e 100%)}
.cover .tan-panel{position:absolute;left:344px;top:46px;width:87px;height:198px;background:var(--tan-soft);border-bottom-right-radius:24px}
.cover .site{position:absolute;left:344px;top:37px;font-size:8px;color:#e3d3c4}
.cover-title{position:absolute;left:26px;top:133px;display:flex;align-items:center;height:19px;font-size:15.5px;letter-spacing:.04em;font-weight:400}
.cover-title .light{color:var(--white);padding-right:5px}
.cover-title .band{background:var(--white);color:var(--tan);padding:0 40px 0 4px;height:19px;line-height:19px;position:relative;width:216px;white-space:nowrap}
.cover-title .band::after{content:"";position:absolute;right:4px;top:2px;width:15px;height:15px;border-radius:50%;background:var(--navy)}
.cover .intro{position:absolute;left:26px;top:155px;width:250px;font-size:4.6px;line-height:6.2px;color:#d9dde0}
.cover .managed{position:absolute;left:347px;top:227px;width:80px;font-size:5.4px;color:var(--navy);line-height:6.2px}
.cover .managed small{display:block;font-size:4.3px;line-height:5.4px}

/* index */
.index .plan{position:absolute;right:0;top:0;width:230px;height:247px;background:linear-gradient(200deg,#dcdfe2 0%,#ebeced 45%,#f2f2f2 100%)}
.index-title{position:absolute;left:26px;top:131px;font-family:"Montserrat",sans-serif;font-weight:900;font-size:25px;color:var(--navy);border-top:2.5px solid var(--navy);padding-top:1px;line-height:26px}
.index-list{position:absolute;left:165px;top:49px;width:248px;list-style:none}
.index-list li{display:flex;align-items:center;height:13.35px;font-size:5.6px;color:var(--ink);white-space:nowrap}
.index-list .num{font-size:8.5px;width:6px}
.index-list .lead{flex:1;border-bottom:1px dashed #6a7785;margin:0 4px 0 2px;height:0}

/* drawings */
.drawings .navy-field{position:absolute;left:0;top:0;width:252px;height:260px;background:var(--navy)}
.slide-title{position:absolute;font-size:13px;letter-spacing:.05em;font-weight:500;color:var(--navy);white-space:nowrap}
.slide-title .accent{color:var(--tan)}
.drawings .slide-title{left:182px;top:36px;color:var(--white)}
.drawings .slide-title .first{color:var(--white)}
.drawings .slide-title .rest{color:var(--tan)}
.drawings .title-bg{position:absolute;left:252px;top:0;width:222px;height:266px;background:var(--paper)}
.drawings .photo-a{left:32px;top:56px;width:141px;height:77px;background:linear-gradient(180deg,#8a8f95,#7a4a3a 60%,#5a3a30)}
.drawings .tan-tab{position:absolute;left:300px;top:56px;width:71px;height:77px;background:var(--tan);border-bottom-right-radius:22px}
.drawings .photo-b{left:182px;top:56px;width:180px;height:77px;background:linear-gradient(180deg,#9aa3ad,#a4766a 55%,#6d5650);border-bottom-right-radius:20px}
.drawings .card{position:absolute;left:26px;top:145px;width:408px;height:94px;background:var(--white);border-bottom-right-radius:34px}
.drawings .card .body-text{position:absolute;left:6px;top:24px;width:210px}
.drawing-sheet{position:absolute;background:linear-gradient(180deg,#f1ef9a 0%,#ecea8f 25%,#f6f6f6 30%,#eef09a 35%,#f6f6f6 55%,#dcdcdc 75%,#f6f6f6 100%);border:1px solid #e2e2e2}
.drawings .drawing-sheet{left:276px;top:5px;width:97px;height:85px}

/* price */
.price .navy-col{position:absolute;left:373px;top:0;width:101px;height:240px;background:var(--navy)}
.price .slide-title{left:69px;top:32px}
.mission{position:absolute;left:13px;top:56px;width:110px;height:195px;background:var(--white);border-bottom-right-radius:24px;padding:20px 4px 0 4px}
.mission h3{font-family:"Montserrat",sans-serif;font-weight:900;font-size:11px;color:var(--navy);letter-spacing:.02em}
.mission p{font-size:4.9px;line-height:6.6px;color:var(--muted);margin-top:28px;padding-left:2px}
.price .tan-panel{position:absolute;left:127px;top:62px;width:284px;height:170px;background:var(--tan);border-bottom-right-radius:24px}
.cost-table{position:absolute;left:130px;top:110px;width:272px;border-collapse:separate;border-spacing:1px 0;font-size:3.2px}
.cost-table th{background:var(--navy);color:var(--white);text-align:left;font-weight:500;height:10.5px;padding:0 3px}
.cost-table td{height:10.8px;padding:0 3px;color:#8a7060}
.cost-table tr:nth-child(even) td{background:#f3ece6}
.cost-table tr:nth-child(odd) td{background:transparent}

/* project */
.project-title{position:absolute;left:172px;top:14px;font-family:"Montserrat",sans-serif;font-weight:900;font-size:25px;line-height:28px;color:var(--navy);letter-spacing:.01em;white-space:nowrap}
.project-title::before{content:"";position:absolute;left:0;top:-2px;width:132px;height:2.5px;background:var(--navy)}
.project-title .num{color:var(--tan)}
.project-a .tan-tab{position:absolute;left:449px;top:25px;width:20px;height:152px;background:var(--tan);border-bottom-right-radius:14px;border-top-left-radius:2px}
.project-a .photo{left:5px;top:46px;width:460px;height:136px;background:linear-gradient(135deg,#556b3f 0%,#6d4032 25%,#8c5040 55%,#c9cdd0 80%,#dfe2e4 100%);border-bottom-right-radius:30px}
.meta{position:absolute;left:8px;font-size:9px}
.meta .label{color:var(--tan);display:inline-block;width:84px;vertical-align:top}
.meta .value{color:var(--navy);display:inline-block;font-weight:500}
.meta.name{top:193px}
.meta.proposal{top:212px}
.meta.proposal .value{font-size:6.8px;width:290px;line-height:8.5px;font-weight:400;color:#44546a}

.project-b .drawing-sheet{left:13px;top:56px;width:168px;height:143px;border:2px solid var(--tan);border-bottom-right-radius:14px}
.project-b .photo{left:191px;top:56px;width:167px;height:143px;background:linear-gradient(160deg,#4f6a4a 0%,#7a5343 35%,#8f5c4a 60%,#b4b8bb 100%);border:2px solid var(--white);border-bottom-right-radius:14px}
.detail-card{position:absolute;left:364px;top:47px;width:89px;height:158px;background:var(--white);border-top:3px solid var(--navy);border-bottom-right-radius:22px;padding:12px 5px 0 6px}
.detail-card h4{font-size:11px;font-weight:500;letter-spacing:.05em;color:var(--navy);white-space:nowrap}
.detail-card p{font-size:4.6px;line-height:6px;color:var(--muted);margin-top:10px}
.col-copy{position:absolute;top:208px;width:155px;text-align:center}
.col-copy h5{font-size:12px;font-weight:500;letter-spacing:.04em;color:var(--navy)}
.col-copy p{font-size:4.4px;line-height:5.6px;color:var(--muted);text-align:left;margin-top:2px}
.col-copy.left{left:20px}.col-copy.right{left:196px}

/* divider */
.divider .photo{inset:0;background:linear-gradient(180deg,#1d2b3b 0%,#1a2635 50%,#15202c 100%)}
.divider .tan-tab{position:absolute;left:453px;top:0;width:21px;height:191px;background:var(--tan);border-bottom-left-radius:14px}
.divider-title{position:absolute;left:0;right:0;top:118px;text-align:center;font-size:26px;letter-spacing:.06em;color:var(--tan);font-weight:400}

/* closing */
.closing .photo{inset:0;background:linear-gradient(180deg,#2a3e54 0%,#2e3d4d 45%,#1c2833 100%)}
.closing .tan-band{position:absolute;left:433px;top:0;width:41px;height:266px;background:var(--tan-soft)}
.closing .logo-panel{position:absolute;left:0;top:87px;width:134px;height:74px;background:var(--white);border-top-right-radius:30px;border-bottom-right-radius:30px;display:flex;align-items:center;justify-content:center;gap:4px}
.closing .logo-panel .wordmark{font-size:15px}
.closing .logo-panel .mark-dot{width:9px;height:9px}
.thanks{position:absolute;left:155px;top:125px;font-size:14px;font-weight:400;letter-spacing:.03em;color:var(--white);white-space:nowrap;border-bottom:1.5px solid var(--tan);padding-bottom:3px;width:278px}
.thanks .accent{color:var(--tan)}
.contact{position:absolute;font-size:7.2px;line-height:9px;color:#b9c2cc;display:flex;gap:6px}
.contact svg{flex:none}
.contact.phone{left:160px;top:158px}
.contact.mail{left:261px;top:156px}
.contact.pin{left:261px;top:174px}
.closing .site{position:absolute;left:320px;top:249px}
</style>
</head>
<body>

<section class="slide cover col-a row-1">
  <div class="photo" role="img" aria-label="Dusk photograph of a white two-storey building with parked cars in front"></div>
  <div class="tan-panel"></div>
  <div class="logo-tab large"><span class="wordmark">BRELMOR</span><span class="mark-dot"></span></div>
  <span class="site">WWW.BRELMOR.CO.UK</span>
  <h1 class="cover-title"><span class="light">INNOVATIVE</span><span class="band">DESIGN SOLUTIONS</span></h1>
  <p class="intro">We are a dynamic architectural firm dedicated to delivering top-tier design and consultation services across a diverse range of sectors. With a profound commitment to innovation and excellence, our company specialises in providing architectural solutions tailored to the unique needs of the Commercial, Residential, Healthcare, and Educational Sectors.</p>
  <p class="managed">Projects managed by<small>Brelmor Innovative Design Solutions Ltd.</small></p>
</section>

<section class="slide index col-b row-1">
  <div class="plan" role="img" aria-label="Faint proposed site plan drawing"></div>
  <div class="logo-tab"><span class="wordmark">BRELMOR</span></div>
  <h2 class="index-title">INDEX</h2>
  <ul class="index-list">
    <li><span class="num">3</span><span class="lead"></span>Creating Working Drawings</li>
    <li><span class="num">5</span><span class="lead"></span>Price Breakdown Of Total Build Costs</li>
    <li><span class="num">7</span><span class="lead"></span>Liaising With Riverline Waters For Water Connection, Drainage Connection</li>
    <li><span class="num">7</span><span class="lead"></span>Liaising With Northway Gas To Get Gas Supply To Site</li>
    <li><span class="num">7</span><span class="lead"></span>Liaising With Central Power Network To Get Electric Supply</li>
    <li><span class="num">7</span><span class="lead"></span>Tendering Out Works To Different Tradesman</li>
    <li><span class="num">7</span><span class="lead"></span>Getting Material Orders</li>
    <li><span class="num">7</span><span class="lead"></span>Arranging Structural Engineer For The Site</li>
    <li><span class="num">7</span><span class="lead"></span>Arranging Building Control For The Site</li>
    <li><span class="num">7</span><span class="lead"></span>Making Sure Material Is On Site On Time</li>
    <li><span class="num">7</span><span class="lead"></span>Making Sure All Tradesman Work Is Up To Current British Standards</li>
    <li><span class="num">7</span><span class="lead"></span>Daily Walk Rounds To Check Work Is Done According To Approved Plans</li>
    <li><span class="num">7</span><span class="lead"></span>Placing Orders For Bathrooms, Kitchen, And Flooring</li>
    <li><span class="num">7</span><span class="lead"></span>All Snag Work With Main Contactor</li>
  </ul>
  <div class="footer-band"><span class="site">WWW.BRELMOR.CO.UK</span><span class="plain-circle"></span></div>
</section>

<section class="slide drawings col-a row-2">
  <div class="navy-field"></div>
  <div class="title-bg"></div>
  <div class="logo-tab"><span class="wordmark">BRELMOR</span></div>
  <h2 class="slide-title"><span class="first">CREATING</span> <span class="rest">WORKING DRAWINGS</span></h2>
  <div class="photo photo-a" role="img" aria-label="Photograph of a red-brick terraced building on a street corner"></div>
  <div class="tan-tab"></div>
  <div class="photo photo-b" role="img" aria-label="Photograph of a brick shopfront building"></div>
  <div class="card">
    <p class="body-text">We are a dynamic architectural firm dedicated to delivering top-tier design and consultation services across a diverse range of sectors. With a profound commitment to innovation and excellence, our company specialises in providing architectural solutions tailored to the unique needs of the Commercial, Residential, Healthcare, and Educational Sectors.</p>
    <div class="drawing-sheet" role="img" aria-label="Architectural drawing sheet with floor plans, elevations and section"></div>
  </div>
  <div class="footer-band"><span class="site">WWW.BRELMOR.CO.UK</span><span class="page-badge">PAGE<br>#</span></div>
</section>

<section class="slide price col-b row-2">
  <div class="navy-col"></div>
  <div class="logo-tab"><span class="wordmark">BRELMOR</span></div>
  <h2 class="slide-title">PRICE BREAKDOWN <span class="accent">OF TOTAL BUILD COSTS</span></h2>
  <div class="mission">
    <h3>OUR MISSION</h3>
    <p>To provide the best service and innovative design solutions to our clients. To help bring their dreams &amp; visions into reality with all the help and support we could offer.</p>
  </div>
  <div class="tan-panel"></div>
  <table class="cost-table">
    <thead><tr><th style="width:58px">Items</th><th>Design Ideas</th><th style="width:14px">Qty.</th><th style="width:38px">Estimated Cost</th></tr></thead>
    <tbody>
      <tr><td>Project</td><td></td><td></td><td></td></tr>
      <tr><td>Frame</td><td></td><td></td><td></td></tr>
      <tr><td>Roof</td><td></td><td></td><td></td></tr>
      <tr><td>Walls</td><td></td><td></td><td></td></tr>
      <tr><td>Fixtures</td><td></td><td></td><td></td></tr>
      <tr><td>Other</td><td></td><td></td><td></td></tr>
    </tbody>
  </table>
  <div class="footer-band"><span class="site">WWW.BRELMOR.CO.UK</span><span class="page-badge">PAGE<br>#</span></div>
</section>

<section class="slide project-a col-a row-3">
  <div class="logo-tab"><span class="wordmark">BRELMOR</span></div>
  <h2 class="project-title">PROJECT <span class="num">- 01</span></h2>
  <div class="tan-tab"></div>
  <div class="photo" role="img" aria-label="Photograph of a brick garage building seen from below with foliage"></div>
  <p class="meta name"><span class="label">Project Name:</span><span class="value">Garages at Ashcombe Mews, Ashcombe Street, Halbrook</span></p>
  <p class="meta proposal"><span class="label">Proposal:</span><span class="value">Proposal: Change of use from garages to two dwelling houses (use class C3) including alterations to the front and side elevations</span></p>
  <div class="footer-band"><span class="site">WWW.BRELMOR.CO.UK</span><span class="page-badge">PAGE<br>#</span></div>
</section>

<section class="slide project-b col-b row-3">
  <div class="logo-tab"><span class="wordmark">BRELMOR</span></div>
  <h2 class="project-title">PROJECT <span class="num">- 01</span></h2>
  <div class="drawing-sheet" role="img" aria-label="Drawing sheet with ground and first floor plans, elevations and section"></div>
  <div class="photo" role="img" aria-label="Photograph of the finished brick mews houses"></div>
  <div class="detail-card">
    <h4>SOME DETAIL</h4>
    <p>To provide the best service and innovative design solutions to our clients. To help bring their dreams &amp; visions into reality with all the help and support we could offer.</p>
  </div>
  <div class="col-copy left"><h5>HEADING</h5><p>We are a dynamic architectural firm dedicated to delivering top-tier design and consultation services across a diverse range of sectors. With a profound commitment to innovation and excellence, Educational Sectors.</p></div>
  <div class="col-copy right"><h5>HEADING</h5><p>We are a dynamic architectural firm dedicated to delivering top-tier design and consultation services across a diverse range of sectors. With a profound commitment to innovation and excellence, Educational Sectors.</p></div>
  <div class="footer-band"><span class="site">WWW.BRELMOR.CO.UK</span><span class="page-badge">PAGE<br>#</span></div>
</section>

<section class="slide divider col-a row-4">
  <div class="photo" role="img" aria-label="Dark rendering of a gabled modern house"></div>
  <div class="tan-tab"></div>
  <div class="logo-tab"><span class="wordmark">BRELMOR</span></div>
  <h2 class="divider-title">DIVIDER PAGE</h2>
  <div class="footer-band"><span class="site">WWW.BRELMOR.CO.UK</span><span class="page-badge">PAGE<br>#</span></div>
</section>

<section class="slide closing col-b row-4">
  <div class="photo" role="img" aria-label="Evening photograph of a modern apartment building with parked cars"></div>
  <div class="tan-band"></div>
  <div class="logo-panel"><span class="wordmark">BRELMOR</span><span class="mark-dot"></span></div>
  <h2 class="thanks">THANK YOU <span class="accent">FOR YOUR BUSINESS!</span></h2>
  <div class="contact phone">
    <svg width="12" height="12" viewBox="0 0 24 24"><path fill="#ffffff" d="M6.6 10.8a15.5 15.5 0 0 0 6.6 6.6l2.2-2.2c.3-.3.7-.4 1-.2 1.1.4 2.3.6 3.6.6.6 0 1 .4 1 1V20c0 .6-.4 1-1 1A17 17 0 0 1 3 4c0-.6.4-1 1-1h3.5c.6 0 1 .4 1 1 0 1.3.2 2.5.6 3.6.1.3 0 .7-.2 1z"/></svg>
    <span>+44 7700 900415<br>+44 7700 900331</span>
  </div>
  <div class="contact mail">
    <svg width="13" height="9" viewBox="0 0 26 18"><rect x="1" y="1" width="24" height="16" fill="none" stroke="#ffffff" stroke-width="1.6"/><path d="M1 1l12 9 12-9" fill="none" stroke="#ffffff" stroke-width="1.6"/></svg>
    <span>info@brelmor.co.uk</span>
  </div>
  <div class="contact pin">
    <svg width="10" height="12" viewBox="0 0 20 24"><path fill="#ffffff" d="M10 0a8 8 0 0 0-8 8c0 6 8 16 8 16s8-10 8-16a8 8 0 0 0-8-8zm0 11a3 3 0 1 1 0-6 3 3 0 0 1 0 6z"/></svg>
    <span>Business Centre<br>Fernley Road Village,<br>Oakhurst, Halbrook HB7 2QX</span>
  </div>
  <span class="site">WWW.BRELMOR.CO.UK</span>
</section>

</body>
</html>
```